Chamber of Commerce Web Design Project

We are working with Harborlight Chamber of Commerce. They are a new chamber of commerce forming in SoCal.
Some sites to use for inspiration:
https://brevinmarchamber.org
https://quellford.org
https://www.dorwickhavenchamber.com
https://www.tpchamber.com
https://velmorintcc.org
Thank you for taking the time to consider designing a website for us. We are web developers based in Stockton, CA, USA. Most of our projects go through the same process. Understanding this process may help you win a project with us. We custom-code all of our websites in-house. We don’t have any requirements as to what tools you use for your design, but we prefer Figma files. For any design that we label as four-stars, we send it to the client for review. The client picks the final design they want us to use. Once we complete this process, we will continue to show additional clients all the four-star sites and purchase them later. Your designs will have multiple chances to sell. For better chances of success, we ask that you follow these guidelines.
IMAGES:
If you use any images or icons in the design, we ask that you have a link to the asset so we can purchase the image/icon. Most of the designs we submit do not have the customer’s images on them unless they have some great images. Be creative; show us the feeling you are trying to portray with your image choices. Use any royalty-free site you choose. We subscribe to Adobe and mainly use their images, but we can purchase images outside of Adobe.
PLEASE NOTE: we will not submit designs to clients with watermarks on the images.
FONTS:
We ask that you identify the fonts used in the design. This can be done in a message if you want. We typically use Google Fonts and Adobe Fonts.
CONTENT:
We're always open to different content and ideas. We often submit designs with stock images so the client can see our vision. We typically take pictures after the website launch to use their images with our vision. Lorem Ipsum is fine for paragraphs, but we ask that you write the headers in correct English. We want to be able to show the vision and identify the sections of the website.
INSPIRATION:
We typically add a couple of links in the brief of websites we like to help you get started in your design.
REVISIONS:
We do not often ask for revisions of the designs unless we see something in the design that may not appeal to the client. If there are slight changes that we want to make, we do that in the development process.
FEEDBACK:
We rarely give feedback on designs during the design process. We are working on many website projects and do not have the time to provide feedback. We usually respond if your request is well thought out and asks specific questions, but a note asking “feedback, please” usually goes unanswered.

```html
<!DOCTYPE html>
<html lang="en">
<head>
<meta charset="utf-8">
<title>Harborlight Chamber of Commerce</title>
<link href="https://fonts.googleapis.com/css2?family=Saira:wght@300;400;600;700;800&family=Roboto:wght@400;500;700&display=swap" rel="stylesheet">
<style>
:root{
  --blue:#0a6cf0;
  --blue-bright:#1a8cff;
  --blue-deep:#0656d6;
  --yellow:#f7c51e;
  --ink:#222;
  --text:#555;
  --muted:#999;
  --light:#f1f2f4;
  --dark:#1c1c1e;
  --white:#fff;
}
*{box-sizing:border-box;margin:0;padding:0}
html,body{width:1200px;height:3961px;overflow:hidden}
body{position:relative;background:var(--white);font-family:"Roboto",sans-serif;color:var(--text)}
.abs{position:absolute}
.head{font-family:"Saira",sans-serif;color:var(--ink);text-transform:uppercase;letter-spacing:1px}
.head .thin{font-weight:300}
.head b{font-weight:700}
.btn{position:absolute;display:flex;align-items:center;justify-content:center;font:700 13px "Roboto",sans-serif;color:var(--white);text-transform:uppercase;clip-path:polygon(8% 0,100% 0,92% 100%,0 100%)}
.btn.blue{background:var(--blue)}
.btn.yellow{background:var(--yellow);color:#1c1c1c}
.btn.dark{background:#1c1c1c}
.photo{position:absolute}
.circle-arrow{position:absolute;border-radius:50%;display:flex;align-items:center;justify-content:center}

/* header */
.topbar{left:0;top:0;width:1200px;height:3px;background:linear-gradient(90deg,var(--blue) 0 400px,var(--yellow) 400px 500px,#bbb 500px)}
.brand{left:143px;top:18px;display:flex;align-items:center;gap:10px;font:800 26px "Saira",sans-serif;color:var(--blue);text-transform:uppercase}
.brand .mark{width:28px;height:28px;border-radius:50%;background:var(--blue)}
.nav{left:480px;top:0;height:74px;display:flex;align-items:center;gap:24px;font-size:13px;color:#333}
.nav .current{position:relative;color:var(--white);padding:0 16px}
.nav .current::before{content:"";position:absolute;left:-4px;right:-4px;top:-28px;bottom:-30px;background:var(--yellow);clip-path:polygon(30% 0,100% 0,70% 100%,0 100%);z-index:-1}

/* hero */
.hero{left:0;top:74px;width:1200px;height:560px;background:linear-gradient(135deg,#1d8bff,#0656e0);overflow:hidden}
.hero-title{left:143px;top:222px;font:800 50px/56px "Saira",sans-serif;color:var(--white);text-transform:uppercase;letter-spacing:1px}
.hero-line{left:143px;top:572px;width:2px;height:120px;background:#e9a43a}

/* about */
.about-text{left:143px;top:794px;width:411px;font-size:13px;line-height:20px;text-align:justify}

/* services */
.services{left:0;top:1192px;width:1200px;height:580px;background:var(--light)}
.svc{position:absolute;top:1334px;width:304px;height:354px;display:flex;flex-direction:column;align-items:center;justify-content:flex-end;padding-bottom:30px;text-align:center}
.svc h3{font:700 19px/24px "Saira",sans-serif;color:var(--white);text-transform:uppercase;letter-spacing:1px}
.svc.active{background:var(--yellow);justify-content:center;padding:0 28px}
.svc.active h3{color:#222}
.svc.active p{font-size:13px;line-height:20px;color:#333;margin:10px 0 18px}

/* programs */
.prog-card{position:absolute;top:2010px;width:228px;height:150px;background:var(--white);padding:14px 14px;box-shadow:0 4px 14px rgba(0,0,0,.06)}
.prog-card h4{font:700 14px/23px "Saira",sans-serif;color:var(--ink);text-transform:uppercase;letter-spacing:0;white-space:nowrap}
.prog-card p{font-size:11px;line-height:16px;margin-top:4px;padding-right:8px}
.prog-card .go{position:absolute;right:8px;bottom:10px;width:26px;height:24px;background:var(--blue);color:#fff;display:flex;align-items:center;justify-content:center}

/* testimonials */
.testi{left:0;top:2253px;width:1200px;height:505px;background:var(--blue)}
.testi-side{top:2456px;width:1200px;height:154px;left:0;background:rgba(255,255,255,.06)}
.side-quote{position:absolute;top:2470px;font-size:12px;line-height:20px;font-style:italic;color:rgba(255,255,255,.35);width:290px}
.testi-card{left:314px;top:2415px;width:573px;height:257px;background:var(--blue-bright);text-align:center;padding-top:70px;box-shadow:0 8px 20px rgba(0,0,0,.1)}
.testi-card p{font-size:13px;line-height:20px;font-style:italic;color:var(--white);padding:0 30px;margin-top:6px}

/* news */
.news{position:absolute;top:2885px;width:288px;height:385px;border:1px solid #ddd;background:#fff;text-align:center}
.news .photo{left:10px;top:10px;width:266px;height:200px}
.news .date{position:absolute;left:50%;transform:translateX(-50%);top:213px;padding:0 20px;height:35px;display:flex;align-items:center;font-size:13px;color:#fff;white-space:nowrap}
.news h4{position:absolute;top:265px;left:20px;right:20px;font:700 13px/20px "Saira",sans-serif;color:var(--ink);text-transform:uppercase;letter-spacing:.5px}
.news p{position:absolute;top:308px;left:20px;right:20px;font-size:13px;line-height:20px}

/* footer */
.footer{left:0;top:3461px;width:1200px;height:500px;background:var(--dark)}
.foot-h{font:700 20px "Saira",sans-serif;color:#fff;text-transform:uppercase}
.links{list-style:none;font-size:13px;color:#fff}
.links li{height:24px;display:flex;align-items:center;gap:12px}
.links li::before{content:"»";color:var(--yellow);font-size:14px}
.contact-list{font-size:13px;line-height:24px;color:#fff;list-style:none}
.contact-list li{display:flex;gap:14px;margin-bottom:24px}
.contact-list svg{flex:none;margin-top:5px}
.form{left:600px;top:3400px;width:455px;height:527px;background:var(--blue)}
.field{position:absolute;left:37px;width:383px;height:57px;background:#fff;font-size:13px;color:#777;padding:18px 20px}
</style>
</head>
<body>

<!-- header -->
<div class="abs topbar"></div>
<div class="abs brand"><span class="mark"></span>Harborlight</div>
<nav class="abs nav">
  <span class="current">Home</span><span>About Us</span><span>Membership</span><span>Program</span><span>Upcoming Events</span><span>Contact</span><span>More <span style="color:var(--yellow)">▾</span></span>
</nav>

<!-- hero -->
<section class="abs hero">
  <div class="photo" role="img" aria-label="Business people shaking hands across a meeting table in a bright office" style="left:0;top:0;width:1200px;height:560px;background:linear-gradient(120deg,#d8dde3,#9aa3ad 60%,#c9ced4);clip-path:polygon(710px 0,1200px 0,1200px 560px,470px 560px)"></div>
  <svg class="abs" style="left:0;top:0" width="1200" height="560"><polygon points="690,0 725,0 490,560 455,560" fill="#f7c51e"/><polygon points="725,0 760,0 525,560 490,560" fill="#0a6cf0"/></svg>
</section>
<h1 class="abs hero-title">Harborlight<br>Chamber<br>of Commerce</h1>
<a class="btn yellow" style="left:146px;top:408px;width:159px;height:37px">Find out more</a>
<div class="circle-arrow" style="left:43px;top:296px;width:38px;height:38px;border:2px solid #fff"><svg width="12" height="8"><path d="M1 7 6 2 11 7" stroke="#fff" stroke-width="2" fill="none"/></svg></div>
<div class="circle-arrow" style="left:43px;top:345px;width:38px;height:38px;background:#fff"><svg width="12" height="8"><path d="M1 1 6 6 11 1" stroke="#0a6cf0" stroke-width="2" fill="none"/></svg></div>
<div class="abs hero-line"></div>

<!-- about -->
<h2 class="abs head" style="left:143px;top:738px;font-size:38px"><span class="thin">About</span> <b>Us</b></h2>
<p class="abs about-text">Lorem ipsum dolor sit amet, consectetur adipiscing elit, sed do eiusmod tempor incididunt ut labore et dolore magna aliqua. Ut enim ad minim veniam, quis nostrud exercitation ullamco laboris nisi ut aliquip ex ea commodo consequat. Duis aute irure dolor in reprehenderit in voluptate velit esse cillum dolore eu fugiat nulla pariatur. Excepteur sint occaecat cupidatat non proident, sunt in culpa qui officia deserunt mollit anim id est laborum. Lorem ipsum dolor sit amet, consectetur adipiscing elit, sed do eiusmod tempor incididunt ut labore et dolore magna aliqua. Ut enim ad minim veniam, quis nostrud exercitation ullamco laboris nisi ut aliquip ex ea commodo consequat.</p>
<a class="btn blue" style="left:146px;top:1027px;width:159px;height:39px">Learn more ➜</a>
<div class="photo" role="img" aria-label="Team meeting around a table in an office" style="left:635px;top:757px;width:211px;height:140px;background:linear-gradient(135deg,#6d7277,#3d4146)"></div>
<div class="photo" role="img" aria-label="Businesswoman smiling while reviewing documents" style="left:883px;top:726px;width:165px;height:212px;background:linear-gradient(135deg,#5a6068,#2f3338)"></div>
<div class="photo" role="img" aria-label="Colleagues greeting with a handshake" style="left:726px;top:929px;width:211px;height:163px;background:linear-gradient(135deg,#4c6a8a,#2a3d52)"></div>

<!-- services -->
<section class="abs services"></section>
<h2 class="abs head" style="left:0;width:1200px;text-align:center;top:1260px;font-size:40px"><span class="thin">Our</span> <b>Services</b></h2>
<div class="svc" role="img" aria-label="Professionals collaborating at a desk, blue tinted" style="left:143px;background:linear-gradient(135deg,#2b78e0,#0d4fb8)"><h3>Business<br>Connections</h3></div>
<div class="svc active" style="left:447px">
  <h3>Government<br>Relations</h3>
  <p>Lorem ipsum dolor sit amet, consectetur adipiscing elit, sed do eiusmod tempor incididunt ut labore et dolore magna aliqua. Ut enim ad minim veniam, quis nostrud exercitation ullamco</p>
  <a class="btn dark" style="position:static;width:150px;height:36px">Learn more ➜</a>
</div>
<div class="svc" role="img" aria-label="Business owner celebrating a success, dark tinted" style="left:751px;background:linear-gradient(135deg,#5c5f63,#2d2f31)"><h3>Small Business<br>Support</h3></div>
<svg class="abs" style="left:68px;top:1500px" width="16" height="22"><path d="M13 2 4 11 13 20" stroke="#222" stroke-width="4" fill="none"/></svg>
<svg class="abs" style="left:1118px;top:1500px" width="16" height="22"><path d="M3 2 12 11 3 20" stroke="#222" stroke-width="4" fill="none"/></svg>

<!-- programs -->
<h2 class="abs head" style="left:141px;top:1840px;font-size:40px;line-height:56px"><span class="thin">Our</span><br><b>Programs</b></h2>
<a class="btn blue" style="left:146px;top:1957px;width:159px;height:38px">View more ➜</a>
<div class="circle-arrow" style="left:143px;top:2036px;width:44px;height:44px;border:1px solid #ccc;color:#333">‹</div>
<div class="circle-arrow" style="left:192px;top:2036px;width:44px;height:44px;border:1px solid #ccc;color:#333">›</div>

<div class="photo" role="img" aria-label="Smiling businesswoman in an office" style="left:418px;top:1852px;width:245px;height:200px;background:linear-gradient(135deg,#c9b39c,#7d6a5b)"></div>
<div class="prog-card" style="left:435px;border:3px solid var(--yellow)"><h4>Business Education<br>Alliance</h4><p>Lorem ipsum dolor sit amet, consec tetur adipiscing elit, sed do eiusmod tempor incididunt ut labore et dolore magna aliqua.</p><span class="go">➜</span></div>
<div class="photo" role="img" aria-label="Two colleagues reviewing a tablet" style="left:688px;top:1852px;width:243px;height:160px;background:linear-gradient(135deg,#d7d9dc,#8f959c)"></div>
<div class="prog-card" style="left:703px"><h4>Certificates of<br>Origin</h4><p>Lorem ipsum dolor sit amet, consec tetur adipiscing elit, sed do eiusmod tempor incididunt ut labore et dolore magna aliqua.</p><span class="go">➜</span></div>
<div style="position:absolute;left:955px;top:1852px;width:245px;height:310px;opacity:.5">
  <div class="photo" role="img" aria-label="Hands joining puzzle pieces" style="left:0;top:0;width:245px;height:160px;background:linear-gradient(135deg,#8c7f74,#4d463f)"></div>
  <div class="prog-card" style="left:17px;top:158px"><h4>Government Relations<br>Council</h4><p>Lorem ipsum dolor sit amet, consec tetur adipiscing elit, sed do eiusmod tempor incididunt ut labore et dolore magna aliqua.</p><span class="go">➜</span></div>
</div>

<!-- testimonials -->
<section class="abs testi"></section>
<div class="abs testi-side"></div>
<p class="side-quote" style="left:30px">"Lorem ipsum dolor sit amet, consectetur adipiscing elit, sed do eiusmod tempor incididunt ut labore et dolore magna aliqua. Ut enim ad minim veniam, quis nostrud exercitation ullamco laboris nisi ut aliquip ex ea commodo occaecat cupidatat non proident, sunt in culpa laborum."</p>
<p class="side-quote" style="left:885px">tetur adipiscing elit, sed do eiusmod tempor aliqua. Ut enim ad minim veniam, quis nostrud quip ex ea commodo consequat. Excepteur sint in culpa qui officia deserunt mollit anim id est laborum."</p>
<h2 class="abs head" style="left:0;width:1200px;text-align:center;top:2310px;font-size:40px;color:#fff"><b>Testimonials</b></h2>
<div class="abs testi-card">
  <div style="color:var(--yellow);font-size:15px;letter-spacing:6px">★★★★★</div>
  <p>“Lorem ipsum dolor sit amet, consectetur adipiscing elit, sed do eiusmod tempor incididunt ut labore et dolore magna aliqua. Ut enim ad minim veniam, quis nostrud exercitation ullamco laboris nisi ut aliquip ex ea commodo consequat. Excepteur sint occaecat cupidatat non proident, sunt in culpa qui officia laborum.”</p>
  <div style="display:flex;align-items:center;justify-content:center;gap:10px;margin-top:10px">
    <div role="img" aria-label="Client portrait" style="width:50px;height:50px;border-radius:50%;border:3px solid #fff;background:#c7b8a9"></div>
    <div style="text-align:left;color:#fff"><div style="font:600 20px 'Saira',sans-serif">John Doe</div><div style="font-size:12px">Company name</div></div>
  </div>
</div>
<svg class="abs" style="left:565px;top:2388px" width="70" height="54"><path d="M4 50V28C4 12 12 4 28 2v10c-8 2-11 6-11 14h11v24z M40 50V28C40 12 48 4 64 2v10c-8 2-11 6-11 14h11v24z" fill="#f7c51e"/></svg>
<div class="circle-arrow" style="left:145px;top:2475px;width:36px;height:36px;background:#fff;color:#333">‹</div>
<div class="circle-arrow" style="left:1019px;top:2475px;width:36px;height:36px;background:#fff;color:#333">›</div>

<!-- news -->
<h2 class="abs head" style="left:0;width:1200px;text-align:center;top:2805px;font-size:40px"><span class="thin">Latest</span> <b>News</b></h2>
<article class="news" style="left:143px"><div class="photo" role="img" aria-label="Colleagues discussing documents at a round table" style="background:linear-gradient(135deg,#cbc7c0,#7a746c)"></div><span class="date" style="background:var(--blue)">▦ JAN 24, 2024</span><h4>Lorem ipsum dolor sit amet,<br>consectetur adipiscing</h4><p>Lorem ipsum dolor sit amet, consectetur adipiscing elit, sed do eiusmod tempor incididunt ut labore</p></article>
<article class="news" style="left:455px"><div class="photo" role="img" aria-label="Business team seated with laptops" style="background:linear-gradient(135deg,#b5b6b8,#6b6d70)"></div><span class="date" style="background:var(--yellow);color:#222">▦ JAN 24, 2024</span><h4>Lorem ipsum dolor sit amet,<br>consectetur adipiscing</h4><p>Lorem ipsum dolor sit amet, consectetur adipiscing elit, sed do eiusmod tempor incididunt ut labore</p></article>
<article class="news" style="left:769px"><div class="photo" role="img" aria-label="Team meeting in a modern office" style="background:linear-gradient(135deg,#6e7c8c,#2f3a47)"></div><span class="date" style="background:#888">▦ JAN 24, 2024</span><h4>Lorem ipsum dolor sit amet,<br>consectetur adipiscing</h4><p>Lorem ipsum dolor sit amet, consectetur adipiscing elit, sed do eiusmod tempor incididunt ut labore</p></article>
<a class="btn blue" style="left:522px;top:3296px;width:159px;height:38px">View more ➜</a>

<!-- footer -->
<footer class="abs footer"></footer>
<svg class="abs" style="left:568px;top:3400px" width="32" height="61"><polygon points="32,0 32,61 0,61" fill="#1a7ee8"/></svg>
<h3 class="abs foot-h" style="left:143px;top:3575px">Quick Links</h3>
<ul class="abs links" style="left:143px;top:3622px">
  <li>Home</li><li>About Us</li><li>Membership</li><li>Program</li><li>Upcoming Events</li><li>Contact</li><li>Privacy policy</li><li>More</li>
</ul>
<h3 class="abs foot-h" style="left:368px;top:3575px">Contact Us</h3>
<ul class="abs contact-list" style="left:368px;top:3622px;width:200px">
  <li><svg width="10" height="14"><path d="M5 0a5 5 0 0 1 5 5c0 4-5 9-5 9S0 9 0 5a5 5 0 0 1 5-5z" fill="#f7c51e"/><circle cx="5" cy="5" r="2" fill="#1c1c1e"/></svg><span style="line-height:24px">123, Lorem ipsum dolor sit consectetur</span></li>
  <li><svg width="12" height="12"><path d="M2 0h3l1 3-2 1.5a8 8 0 0 0 3.5 3.5L9 6l3 1v3c0 1-1 2-2 2A10 10 0 0 1 0 2c0-1 1-2 2-2z" fill="#f7c51e"/></svg>+1 888 888 8888</li>
  <li><svg width="12" height="12"><rect x="0" y="3" width="12" height="9" fill="#f7c51e"/><rect x="3" y="0" width="6" height="4" fill="#f7c51e"/></svg>+44 (0)1632 960418</li>
  <li><svg width="12" height="10"><rect width="12" height="10" fill="#f7c51e"/><path d="M0 0 6 5 12 0" stroke="#1c1c1e" fill="none"/></svg>info@companyname.com</li>
</ul>
<p class="abs" style="left:143px;top:3878px;font-size:13px;color:#fff">© Copyrights 2025 | All Rights Reserved</p>

<form class="abs form">
  <h2 class="head" style="text-align:center;margin-top:32px;font-size:38px;color:#fff"><span class="thin">Get</span> <b>in Touch</b></h2>
  <div class="field" style="top:100px">Name</div>
  <div class="field" style="top:164px">Email</div>
  <div class="field" style="top:228px">Phone</div>
  <div class="field" style="top:292px;height:130px">Message</div>
  <a class="btn yellow" style="left:150px;top:436px;width:158px;height:38px">Submit</a>
</form>

</body>
</html>
```